Coastal Learner Bureau business cards

Australian company about to start offering its services. We recruit international students to come to study English, vocational education and postgraduate courses in Australia. We help them find the institution and select the right city they want to come to Australia. We are a young, online oriented and supportive agency. Our clients are between 18 and 35 years old, mainly University students, young professionals or people with work experience. We provide much more information that any other agency offer. We administrate a Facebook group with more than 11.000 members that daily ask questions about general information when coming to Australia, while they are here and even after they leave the country

Target Market(s)

International students from South America, Central America and Europe

Industry/Entity Type

Student

Contact Information for Business Card

Tomas Bilbrea
Managing Director
tomas@kelvarin.com.au
www.kelvoria.com.au
+61 491058264
Melbourne, Australia

Font styles to use
Serif
Sans Serif

Colors

Designer to choose colors to be used in the design.

Requirements
Must have
• Horizontal design
• Standard business card size and shape. If font uses green or yellow colours, they will have to match the ones from the logo
Nice to have
• UPDATE: Use the contents of the green image to design one of the card sides. Use our logo in the background of that side as watermark.
• Passport image, or immigration stamps. A picture of the Yarra River (from Melbourne) would be cool as well.
Should not have
• Non-standard business card size and shape
• Not black as the background colour of any sides as we are not a VIP agency or a hight class service. We are orientes to young people and they like colours, pictures, something attractive.
• Vertical design
• NO YELLOW or BLACK AS THE BACKGROUND COLOUR OF ANY SIDE OF THE BIZ CARD

```html
<!DOCTYPE html>
<html lang="es">
<head>
<meta charset="utf-8">
<title>Coastal Learner Bureau – Business Cards</title>
<link rel="stylesheet" href="https://fonts.googleapis.com/css2?family=Lato:wght@400;700&family=Mulish:wght@800&display=swap">
<style>
  :root {
    --stage: #1b1b1b;
    --paper: #f2f2f2;
    --brand-green: #17613f;
    --ink-green: #0f5a35;
    --brand-yellow: #e8b417;
    --ink: #1a1a1a;
    --white: #ffffff;
  }
  * { margin: 0; padding: 0; box-sizing: border-box; }
  html, body {
    width: 1200px; height: 900px; overflow: hidden;
    background: var(--stage);
  }
  .stage { position: relative; width: 1200px; height: 900px; }

  .card {
    position: absolute; left: 319px; width: 561px; height: 347px;
    overflow: hidden; text-align: center;
  }
  .card--front { top: 91px; background: var(--paper); }
  .card--back { top: 462px; background: var(--brand-green); }

  .wordmark {
    display: flex; align-items: center; justify-content: center; gap: 10px;
    font-family: "Lato", sans-serif; font-weight: 700; letter-spacing: 0.5px;
    line-height: 1;
  }
  .wordmark__dot {
    width: 14px; height: 14px; border-radius: 50%;
    background: var(--brand-yellow);
  }
  .tagline {
    font-family: "Mulish", sans-serif; font-weight: 800; font-size: 20px;
    letter-spacing: 0.2px; line-height: 1;
  }

  /* front */
  .brand-block {
    position: absolute; left: 0; top: 0; width: 300px; height: 347px;
    display: flex; flex-direction: column; justify-content: center; gap: 30px;
  }
  .card--front .wordmark { font-size: 46px; color: var(--ink-green); }
  .card--front .tagline { color: var(--ink-green); }

  .divider {
    position: absolute; left: 300px; top: 60px; width: 1px; height: 227px;
    background: var(--brand-green);
  }

  .details {
    position: absolute; left: 301px; top: 0; width: 260px; height: 347px;
    display: flex; flex-direction: column; justify-content: center;
    font-family: "Lato", sans-serif;
  }
  .holder__name { font-size: 19px; line-height: 23px; color: var(--ink-green); }
  .holder__first { color: var(--brand-yellow); }
  .holder__role { font-size: 15px; line-height: 18px; color: var(--ink); }
  .holder__rule {
    width: 113px; height: 1px; margin: 14px auto 0;
    background: var(--brand-green);
  }
  .contact-icons {
    display: flex; justify-content: center; gap: 5px; margin-top: 16px;
  }
  .contact-icons svg { width: 11px; height: 11px; fill: var(--brand-green); }
  .contact {
    margin-top: 10px; list-style: none;
    font-size: 15px; line-height: 20.5px; color: var(--ink);
  }
  .contact__city { margin-top: 19px; }

  /* back */
  .backdrop-disc {
    position: absolute; width: 360px; height: 360px; border-radius: 50%;
    left: 260px; top: -90px; background: rgba(255,255,255,0.035);
  }
  .back-block {
    position: absolute; inset: 0;
    display: flex; flex-direction: column; justify-content: center; gap: 34px;
  }
  .card--back .wordmark { font-size: 54px; color: var(--white); }
  .card--back .tagline { font-size: 21px; color: var(--brand-yellow); }
</style>
</head>
<body>
<main class="stage">
  <section class="card card--front" aria-label="Card front">
    <div class="brand-block">
      <div class="wordmark"><span>Kelvoria</span><span class="wordmark__dot"></span></div>
      <p class="tagline">HACEMOS MÁS POR TI!</p>
    </div>
    <div class="divider"></div>
    <div class="details">
      <p class="holder__name"><span class="holder__first">TOMAS</span> BILBREA</p>
      <p class="holder__role">Managing Director</p>
      <div class="holder__rule"></div>
      <div class="contact-icons" aria-hidden="true">
        <svg viewBox="0 0 24 24"><path d="M6.6 10.8a15.2 15.2 0 0 0 6.6 6.6l2.2-2.2a1 1 0 0 1 1-.25 11.4 11.4 0 0 0 3.6.6 1 1 0 0 1 1 1V20a1 1 0 0 1-1 1A17 17 0 0 1 3 4a1 1 0 0 1 1-1h3.5a1 1 0 0 1 1 1c0 1.25.2 2.45.6 3.6a1 1 0 0 1-.25 1z"/></svg>
        <svg viewBox="0 0 24 24"><rect x="2" y="5" width="20" height="14"/><path d="M2.5 5.5 12 12.5l9.5-7" stroke="#f2f2f2" stroke-width="1.8" fill="none"/></svg>
        <svg viewBox="0 0 24 24"><circle cx="12" cy="12" r="10"/><path d="M2 12h20M12 2c3 3 3 17 0 20M12 2c-3 3-3 17 0 20" stroke="#f2f2f2" stroke-width="1.4" fill="none"/></svg>
      </div>
      <ul class="contact">
        <li>+61 491058264</li>
        <li>tomas@kelvarin.com.au</li>
        <li>www.kelvoria.com.au</li>
        <li class="contact__city">Melbourne, Australia</li>
      </ul>
    </div>
  </section>

  <section class="card card--back" aria-label="Card back">
    <div class="backdrop-disc" aria-hidden="true"></div>
    <div class="back-block">
      <div class="wordmark"><span>Kelvoria</span><span class="wordmark__dot"></span></div>
      <p class="tagline">HACEMOS MÁS POR TI!</p>
    </div>
  </section>
</main>
</body>
</html>
```